Design concept Visual UI of future mobile app - healthcare

Hi,
I'm looking for a top designer, innovative with strong experience in user interface

The app will be connected to a future health website related to depression and addiction by helping the user to track the moods, tired, anxiety using this mobile app.

I attached the deck of the overall project but I can send you a specific presentation for the app only

thanks

Target Market(s)

Switzerland, UK, Germany and France

Industry/Entity Type

Mental Health

Logo Text

Health, hope

Font styles to use
Sans Serif

Colors
cee9f5
33a6d7
0692cd
0255a3
3276b5
85abd2

Requirements
Must have
• keep it simple, easy to navigate
• The user should be able to track the moods on a daily basis,
• sleep time, and rate how the feel on the day
• To be able to get information from the sync deck of vexlo
Nice to have
• to be able share this app with a friend

```html
<!DOCTYPE html>
<html lang="en">
<head>
<meta charset="utf-8">
<title>Calmora – App Screens</title>
<link rel="stylesheet" href="https://fonts.googleapis.com/css2?family=Roboto:wght@400;500;700&display=swap">
<style>
:root{
  --page:#f1f1f1;
  --sky:#c5e4f2;
  --blue:#33a6d7;
  --blue-text:#2f86c6;
  --blue-deep:#0255a3;
  --blue-mid:#3276b5;
  --screen-top:#f2f2f2;
  --screen-bottom:#dcdcdc;
  --ink:#222;
  --white:#fff;
}
*{box-sizing:border-box;margin:0;padding:0}
html,body{width:1200px;height:800px;overflow:hidden}
body{background:var(--page);font-family:"Roboto",sans-serif;position:relative}
.screen{position:absolute;top:228px;width:189px;height:334px;overflow:hidden;
  background:linear-gradient(var(--screen-top),var(--screen-bottom));
  border:1px solid #2a2a2a}
.screen--home{left:233px}
.screen--mood{left:510px}
.screen--graphs{left:786px}
.status{height:12px;display:flex;align-items:center;justify-content:space-between;
  padding:0 5px;font-size:6px;color:var(--white);background:#1b1b1b}
.status--light{background:var(--white);color:var(--ink)}
.status .battery{display:inline-block;width:11px;height:5px;border:1px solid currentColor;
  margin-left:2px;vertical-align:middle;background:currentColor}
.topbar{position:relative;height:30px;background:var(--sky)}
.topbar .menu{position:absolute;left:11px;top:10px}
.topbar .arrow{position:absolute;top:8px;font-size:11px;line-height:11px;color:var(--white)}
.topbar .arrow--prev{left:42px}
.topbar .arrow--next{right:14px}
.topbar h1{position:absolute;left:0;right:0;top:9px;text-align:center;font-weight:400;
  font-size:11px;line-height:12px;color:var(--blue)}
.topbar h1.caps{font-size:8.5px;top:10px;letter-spacing:.2px;font-weight:500}
.menu{width:12px;display:flex;flex-direction:column;gap:2px}
.menu i{display:block;height:2px;background:var(--blue-mid)}
.brand{text-align:center;margin-top:21px}
.brand .mark{width:30px;height:30px;border-radius:50%;background:var(--blue-mid);margin:0 auto}
.brand .name{margin-top:6px;font-size:13px;font-weight:700;color:var(--blue-text);letter-spacing:.3px}
.nav{display:flex;flex-direction:column;align-items:center;gap:9px;margin-top:15px}
.btn{width:96px;height:12px;border-radius:2px;font-size:6.5px;color:var(--white);
  display:flex;align-items:center;justify-content:center;
  background:linear-gradient(#3d8cc8,var(--blue-deep))}
.claim{margin-top:12px;text-align:center;font-size:8px;line-height:10.5px;font-weight:700;color:var(--blue-text)}
.messages{margin:10px auto 0;width:96px;height:14px;border-radius:2px;background:linear-gradient(#fafafa,#dedede);
  border:1px solid #cfcfcf;font-size:6px;font-weight:700;color:var(--blue-mid);
  display:flex;align-items:center;justify-content:center}
.sleep-card{margin:9px auto 0;width:95px;height:51px;border-radius:3px;
  background:linear-gradient(#3f9bd6,var(--blue-deep));color:var(--white);text-align:center;padding-top:5px}
.sleep-card h2{font-size:7px;font-weight:700}
.sleep-card p{font-size:5.5px;margin-top:3px}
.sleep-card .ok{width:44px;height:13px;margin:6px auto 0;background:var(--white);border-radius:2px;
  color:var(--blue-mid);font-size:6px;font-weight:700;display:flex;align-items:center;justify-content:center}
.avatar{width:28px;height:32px;margin:15px auto 0;background:linear-gradient(#b98a5c,#e4c3a3);border:1px solid var(--white)}
.question{text-align:center;font-size:11px;line-height:13px;color:var(--blue);margin-top:3px}
.moods{list-style:none;margin:3px auto 0;width:155px}
.moods li{height:17.7px;display:flex;align-items:center;justify-content:center;font-size:8.5px;color:var(--white)}
.moods li:nth-child(1){background:#e8410a}
.moods li:nth-child(2){background:#ee660c}
.moods li:nth-child(3){background:#e2850f}
.moods li:nth-child(4){background:#dcaa2f}
.moods li:nth-child(5){background:#a59a19}
.moods li:nth-child(6){background:#909716}
.moods li:nth-child(7){background:#828f22}
.moods li:nth-child(8){background:#77832e}
.moods li:nth-child(9){background:#6f7536}
.moods li:nth-child(10){background:#6e6f60}
.sleep-time{display:flex;justify-content:flex-end;align-items:center;gap:3px;margin:6px 20px 0 0}
.sleep-time span.label{font-size:9px;font-weight:700;color:var(--blue);margin-right:3px}
.sleep-time b{width:14px;height:14px;background:var(--blue-mid);color:var(--white);font-size:7px;
  font-weight:500;display:flex;align-items:center;justify-content:center;border-radius:2px}
.chart-title{text-align:center;font-size:6.5px;font-weight:700;color:var(--blue-mid);margin-top:9px}
.chart{display:block;margin:5px auto 0;width:139px;height:99px}
.axis{display:flex;justify-content:space-between;width:136px;margin:3px auto 0;font-size:4.2px;color:#555;text-align:center;line-height:5px}
</style>
</head>
<body>

<section class="screen screen--home">
  <div class="status"><span>●●●○○ NOVA</span><span>4:21 PM</span><span>100% <i class="battery"></i></span></div>
  <header class="topbar"><div class="menu"><i></i><i></i><i></i></div><span class="arrow arrow--next">›</span></header>
  <div class="brand"><div class="mark"></div><div class="name">CALMORA</div></div>
  <nav class="nav">
    <div class="btn">Whats New Today?</div>
    <div class="btn">Tracking Graphs</div>
    <div class="btn">Personal Information</div>
  </nav>
  <p class="claim">According to our studies<br>Calmora App has potential<br>to improve your mood by 16%</p>
  <div class="messages">You have 03 messages</div>
  <div class="sleep-card"><h2>Sleep Time</h2><p>Do you want to sleep ?</p><div class="ok">OK</div></div>
</section>

<section class="screen screen--mood">
  <div class="status status--light"><span>●●●○○ NOVA</span><span>4:21 PM</span><span>100% <i class="battery"></i></span></div>
  <header class="topbar"><div class="menu"><i></i><i></i><i></i></div><span class="arrow arrow--prev">‹</span><h1>Whats New Today?</h1><span class="arrow arrow--next">›</span></header>
  <div class="avatar" role="img" aria-label="User profile photo"></div>
  <p class="question">How do you feel today ?</p>
  <ul class="moods">
    <li>Insanely Great</li><li>Great</li><li>Very good</li><li>Good</li><li>Okay</li>
    <li>So-so</li><li>Meh</li><li>Bad</li><li>Very bad</li><li>Couldn't be worse</li>
  </ul>
  <div class="sleep-time"><span class="label">Sleep Time</span><b>08</b><b>30</b><b>30</b></div>
</section>

<section class="screen screen--graphs">
  <div class="status"><span>●●●○○ NOVA</span><span>4:21 PM</span><span>100% <i class="battery"></i></span></div>
  <header class="topbar"><div class="menu"><i></i><i></i><i></i></div><span class="arrow arrow--prev">‹</span><h1 class="caps">TRACKING GRAPHS</h1><span class="arrow arrow--next">›</span></header>
  <p class="chart-title">WEEK</p>
  <svg class="chart" viewBox="0 0 139 99" aria-label="Weekly mood chart">
    <rect y="0" width="139" height="10" fill="#e8410a"/>
    <rect y="10" width="139" height="10" fill="#ec6212"/>
    <rect y="20" width="139" height="10" fill="#e2850f"/>
    <rect y="30" width="139" height="10" fill="#d9a52c"/>
    <rect y="40" width="139" height="10" fill="#a59a19"/>
    <rect y="50" width="139" height="10" fill="#909716"/>
    <rect y="60" width="139" height="10" fill="#828f22"/>
    <rect y="70" width="139" height="10" fill="#77832e"/>
    <rect y="80" width="139" height="10" fill="#6f7536"/>
    <rect y="90" width="139" height="9" fill="#6e6f60"/>
    <g stroke="#fff" stroke-opacity=".15" stroke-width=".5">
      <path d="M11.6 0V99M23.2 0V99M34.8 0V99M46.4 0V99M58 0V99M69.6 0V99M81.2 0V99M92.8 0V99M104.4 0V99M116 0V99M127.6 0V99"/>
    </g>
    <polyline fill="none" stroke="#fff" stroke-width=".8" points="8,55 19,64 30,34 41,25 52,45 63,54 75,44 86,34 97,44 108,15 120,64 131,74"/>
    <g fill="#fff">
      <circle cx="8" cy="55" r="1.5"/><circle cx="19" cy="64" r="1.5"/><circle cx="30" cy="34" r="1.5"/><circle cx="41" cy="25" r="1.5"/>
      <circle cx="52" cy="45" r="1.5"/><circle cx="63" cy="54" r="1.5"/><circle cx="75" cy="44" r="1.5"/><circle cx="86" cy="34" r="1.5"/>
      <circle cx="97" cy="44" r="1.5"/><circle cx="108" cy="15" r="1.5"/><circle cx="120" cy="64" r="1.5"/><circle cx="131" cy="74" r="1.5"/>
    </g>
  </svg>
  <div class="axis">
    <span>Mon<br>21/5</span><span>Tue<br>22/5</span><span>Wed<br>23/5</span><span>Thu<br>24/5</span><span>Fri<br>25/5</span><span>Sat<br>26/5</span>
    <span>Sun<br>27/5</span><span>Mon<br>28/5</span><span>Tue<br>29/5</span><span>Wed<br>30/5</span><span>Thu<br>31/5</span><span>Fri<br>1/6</span>
  </div>
  <p class="chart-title" style="margin-top:13px">MONTH 2015</p>
  <svg class="chart" viewBox="0 0 139 99" aria-label="Monthly mood chart">
    <defs>
      <linearGradient id="month-fill" x1="0" y1="0" x2="0" y2="1">
        <stop offset="0" stop-color="#e8410a"/>
        <stop offset=".25" stop-color="#ee7a14"/>
        <stop offset=".45" stop-color="#d8a52a"/>
        <stop offset=".6" stop-color="#8f9619"/>
        <stop offset="1" stop-color="#77832e"/>
      </linearGradient>
    </defs>
    <rect width="139" height="99" fill="url(#month-fill)"/>
    <g stroke="#fff" stroke-opacity=".15" stroke-width=".5">
      <path d="M11.6 0V99M23.2 0V99M34.8 0V99M46.4 0V99M58 0V99M69.6 0V99M81.2 0V99M92.8 0V99M104.4 0V99M116 0V99M127.6 0V99"/>
    </g>
    <line x1="0" y1="49" x2="139" y2="49" stroke="#fff" stroke-width=".7"/>
    <path fill="none" stroke="#fff" stroke-width=".8" d="M0 48C6 44 10 42 16 40S26 36 32 38 40 30 46 32 54 28 60 34 68 36 74 40 82 42 88 46 96 60 100 52 106 30 112 32 120 38 126 36 134 34 139 34"/>
  </svg>
  <div class="axis" style="font-size:4.6px"><span>Jan</span><span>Feb</span><span>Mar</span><span>Apr</span><span>May</span><span>Jun</span><span>Jul</span><span>Aug</span><span>Sep</span><span>Oct</span><span>Nov</span><span>Dec</span></div>
</section>

</body>
</html>
```